Redesign of the UI of a customer service platform

To improve the user experience of our customers, we need a new design for our agent interface of our customer service platform (velorant.com).
The focus will be on the dashboard and the inbox screens (see attached) along with the common UI elements (Buttons, menu, fonts, forms...)
We want a simple and distinctive design

Target Market(s)

Worldwide

Industry/Entity Type

It Service

Number of Pages Required

3 page

Font styles to use
Sans Serif

Requirements
Must have
• New Onboarding page: this is a new page that is shown to user the first time they login to the platform. This will replace the current onboarding screen (setup SMS, Setup widget...etc)
• Dashboard page: to access important information and activate services (see screenshot from current site)
• Inbox page: to manage all the interactions with customers. (see screenshot from current site)
• UI elements (buttons, menus, forms, tables, fonts, color palette)

```html
<!DOCTYPE html>
<html lang="en">
<head>
<meta charset="utf-8">
<title>Velorant — Onboarding</title>
<link href="https://fonts.googleapis.com/css2?family=Lato:wght@400;700&display=swap" rel="stylesheet">
<style>
:root{
  --brand:#f15a24;
  --bg:#f2f2f2;
  --panel:#ffffff;
  --text:#333333;
  --muted:#888888;
  --nav-icon:#9a9a9a;
  --sky:#00bfee;
  --amber:#fbba3b;
  --leaf:#7ac143;
  --blue:#3a84c0;
  --orange:#f29d12;
  --green:#1aa34a;
  --ring:#d9d9d9;
  --badge-red:#e30613;
  --badge-yellow:#f7b500;
}
*{box-sizing:border-box;margin:0;padding:0}
html,body{width:1200px;height:919px;overflow:hidden}
body{background:var(--bg);font-family:'Lato',sans-serif;color:var(--text);position:relative}
.topbar{position:absolute;left:0;top:0;width:1200px;height:83px;background:var(--panel);display:flex}
.brand{width:83px;height:83px;background:var(--brand);color:#fff;display:flex;align-items:center;justify-content:center;font-size:13px;font-weight:700}
.nav-item{width:84px;height:83px;border-right:1px solid #eee;display:flex;flex-direction:column;align-items:center;justify-content:center;gap:6px;color:var(--muted);font-size:13px;position:relative}
.nav-item svg{width:28px;height:28px}
.count{position:absolute;top:17px;left:50px;width:22px;height:22px;border-radius:50%;color:#fff;font-size:12px;display:flex;align-items:center;justify-content:center}
.count.red{background:var(--badge-red)}
.count.yellow{background:var(--badge-yellow)}
.avatar{position:absolute;right:15px;top:14px;width:55px;height:55px;border-radius:50%;background:linear-gradient(#d8c8b8,#8a6b58)}
.online{position:absolute;right:62px;top:15px;width:13px;height:13px;border-radius:50%;background:#2db84b}
.panel{position:absolute;top:97px;height:453px;background:var(--panel)}
.start{left:14px;width:752px}
.start h2{font-weight:400;font-size:20px;text-align:center;margin-top:23px}
.video{position:absolute;left:28px;top:69px;width:697px;height:327px;background:linear-gradient(135deg,#c9c0b0 0%,#9b8470 40%,#5a4a3e 75%,#2f2a28 100%)}
.play{position:absolute;left:314px;top:128px;width:70px;height:70px;border-radius:50%;background:rgba(255,255,255,.9);display:flex;align-items:center;justify-content:center}
.player{position:absolute;left:28px;top:410px;width:697px;display:flex;align-items:center;gap:8px;font-size:12px;color:#aaa}
.track{flex:1;height:3px;background:#ddd;position:relative;margin-left:4px}
.track span{position:absolute;left:0;top:0;height:3px;width:36%;background:var(--brand)}
.plan{left:780px;width:406px;padding:23px 28px}
.plan-head h3{font-weight:400;font-size:21px}
.plan-head h3 small{font-size:13px;color:var(--muted)}
.plan-head p{font-size:13px;color:var(--muted);margin-top:3px}
.buy{position:absolute;right:28px;top:26px;width:101px;height:35px;background:var(--brand);color:#fff;font-size:13px;display:flex;align-items:center;justify-content:center}
.quota{position:absolute;left:28px;width:351px;height:106px;color:#fff;display:flex}
.quota .ico{width:105px;display:flex;align-items:center;justify-content:center;border-right:1px solid rgba(255,255,255,.25);margin:10px 0}
.quota .info{padding:17px 0 0 28px;flex:1}
.quota h4{font-weight:400;font-size:19px}
.quota p{font-size:13px;margin-top:12px}
.quota .ratio{position:absolute;right:18px;top:26px;font-size:13px}
.agents{top:88px;background:var(--sky)}
.depts{top:203px;background:var(--amber)}
.phones{top:318px;background:var(--leaf)}
.addons-title{position:absolute;top:592px;width:1200px;text-align:center;font-weight:400;font-size:21px}
.addon{position:absolute;top:661px;width:150px;text-align:center}
.addon svg.ringset{display:block;margin:0 auto}
.addon h5{font-weight:400;font-size:19px;margin-top:22px}
.addon a{display:inline-block;margin-top:10px;font-size:13px;color:var(--brand);text-decoration:none}
.tick{position:absolute;left:16px;top:-1px}
</style>
</head>
<body>
<header class="topbar">
  <div class="brand">velorant</div>
  <div class="nav-item"><svg viewBox="0 0 28 28"><path d="M3 14h6l2 4h6l2-4h6v10H3z" fill="var(--nav-icon)"/><path d="M14 3v10M10 9l4 4 4-4" stroke="var(--nav-icon)" stroke-width="2" fill="none"/></svg>Inbox<span class="count red">4</span></div>
  <div class="nav-item"><svg viewBox="0 0 28 28"><rect x="4" y="3" width="18" height="22" fill="none" stroke="var(--nav-icon)" stroke-width="2"/><path d="M8 9h10M8 13h10M8 17h6" stroke="var(--nav-icon)" stroke-width="2"/></svg>Tasks<span class="count yellow">1</span></div>
  <div class="nav-item"><svg viewBox="0 0 28 28"><circle cx="14" cy="9" r="5" fill="var(--nav-icon)"/><path d="M5 25c0-7 4-10 9-10s9 3 9 10z" fill="var(--nav-icon)"/></svg>Customers</div>
  <div class="nav-item"><svg viewBox="0 0 28 28"><path d="M3 5l22 9-22 9 4-9z" fill="none" stroke="var(--nav-icon)" stroke-width="2" stroke-linejoin="round"/><path d="M7 14h18" stroke="var(--nav-icon)" stroke-width="2"/></svg>Campaigns</div>
  <div class="nav-item"><svg viewBox="0 0 28 28"><text x="14" y="22" font-size="24" text-anchor="middle" fill="var(--nav-icon)" font-family="Lato,sans-serif">$</text></svg>Payments</div>
  <div class="nav-item"><svg viewBox="0 0 28 28"><path d="M4 4v20M10 10v14M16 4v20M22 14v10" stroke="var(--nav-icon)" stroke-width="3"/></svg>Reports</div>
  <div class="nav-item"><svg viewBox="0 0 28 28"><circle cx="14" cy="14" r="8" fill="none" stroke="var(--nav-icon)" stroke-width="5" stroke-dasharray="4 2.3"/><circle cx="14" cy="14" r="6" fill="none" stroke="var(--nav-icon)" stroke-width="3"/></svg>Settings</div>
  <div class="avatar" role="img" aria-label="Agent profile photo"></div>
  <span class="online"></span>
</header>

<section class="panel start">
  <h2>Get Started</h2>
  <div class="video" role="img" aria-label="Photo of colleagues planning at a desk with notes and a notebook">
    <div class="play"><svg width="20" height="22" viewBox="0 0 20 22"><path d="M2 1l17 10L2 21z" fill="var(--brand)"/></svg></div>
  </div>
  <div class="player"><svg width="8" height="10"><path d="M0 0l8 5-8 5z" fill="#aaa"/></svg>0:00<div class="track"><span></span></div></div>
</section>

<section class="panel plan">
  <div class="plan-head"><h3>Plan <small>(Trial)</small></h3><p>Your trial period ends in 14 days</p></div>
  <div class="buy">BUY NOW</div>
  <div class="quota agents">
    <div class="ico"><svg width="60" height="52" viewBox="0 0 60 52" fill="#fff"><circle cx="14" cy="12" r="8"/><circle cx="46" cy="12" r="8"/><circle cx="30" cy="20" r="9"/><path d="M0 36c0-10 6-14 14-14 4 0 6 1 8 2-4 3-6 8-6 14H0zM60 36c0-10-6-14-14-14-4 0-6 1-8 2 4 3 6 8 6 14h16zM14 52c0-13 7-18 16-18s16 5 16 18z"/></svg></div>
    <div class="info"><h4>Agents</h4><p>Up to 3</p></div><span class="ratio">1/3</span>
  </div>
  <div class="quota depts">
    <div class="ico"><svg width="60" height="48" viewBox="0 0 60 48" fill="#fff"><path d="M22 0h16a4 4 0 0 1 4 4v4h-4V4H22v4h-4V4a4 4 0 0 1 4-4z"/><rect x="0" y="10" width="60" height="14" rx="3"/><rect x="0" y="27" width="60" height="21" rx="3"/><circle cx="30" cy="25" r="4" fill="var(--amber)" stroke="#fff" stroke-width="2"/></svg></div>
    <div class="info"><h4>Departments</h4><p>Up to 3</p></div><span class="ratio">1/3</span>
  </div>
  <div class="quota phones">
    <div class="ico"><svg width="60" height="60" viewBox="0 0 60 60"><path d="M8 4l10 14-6 6c4 10 12 18 22 22l6-6 14 10-6 8C22 56 4 38 2 10z" fill="#fff"/></svg></div>
    <div class="info"><h4>Phones</h4><p>Up to 1</p></div><span class="ratio">0/1</span>
  </div>
</section>

<h2 class="addons-title">Select Your Add-ons</h2>

<div class="addon" style="left:161px">
  <svg class="ringset" width="146" height="146" viewBox="0 0 146 146"><circle cx="73" cy="73" r="71" fill="none" stroke="var(--ring)" stroke-width="3"/><circle cx="73" cy="73" r="71" fill="none" stroke="var(--sky)" stroke-width="3.5" stroke-dasharray="149 446" transform="rotate(60 73 73)"/><rect x="45" y="50" width="56" height="38" rx="2" fill="var(--sky)"/><rect x="49" y="54" width="48" height="26" fill="#fff"/><rect x="51" y="56" width="44" height="22" fill="var(--sky)"/><path d="M68 88h10v6H68zM60 96h26" stroke="var(--sky)" stroke-width="3"/></svg>
  <h5>Campaigns</h5><a href="#">⊙ Watch Video</a>
</div>
<div class="addon" style="left:343px">
  <svg class="ringset" width="146" height="146" viewBox="0 0 146 146"><circle cx="73" cy="73" r="71" fill="none" stroke="var(--ring)" stroke-width="3"/><circle cx="73" cy="73" r="71" fill="none" stroke="var(--blue)" stroke-width="3.5" stroke-dasharray="149 446" transform="rotate(60 73 73)"/><circle cx="73" cy="73" r="20" fill="var(--blue)"/></svg>
  <h5>Chatline</h5><a href="#">⊙ Watch Video</a>
</div>
<div class="addon" style="left:526px">
  <svg class="ringset" width="146" height="146" viewBox="0 0 146 146"><circle cx="73" cy="73" r="71" fill="none" stroke="var(--ring)" stroke-width="3"/><circle cx="73" cy="73" r="71" fill="none" stroke="var(--orange)" stroke-width="3.5" stroke-dasharray="149 446" transform="rotate(60 73 73)"/><path d="M73 50c15 0 26 8 26 19s-11 19-26 19c-3 0-5 0-7-1l-14 7 4-10c-5-4-8-9-8-15 0-11 11-19 25-19z" fill="var(--orange)"/><path d="M61 63h24M61 69h24M61 75h24" stroke="#fff" stroke-width="2"/></svg>
  <svg class="tick" width="28" height="28" viewBox="0 0 28 28"><path d="M14 1l4 3 5 0 1 5 3 4-3 4-1 5-5 0-4 3-4-3-5 0-1-5-3-4 3-4 1-5 5 0z" fill="var(--green)"/><path d="M8 14l4 4 8-8" stroke="#fff" stroke-width="2.5" fill="none"/></svg>
  <h5>SMS</h5><a href="#">⊙ Watch Video</a>
</div>
<div class="addon" style="left:708px">
  <svg class="ringset" width="146" height="146" viewBox="0 0 146 146"><circle cx="73" cy="73" r="71" fill="none" stroke="var(--ring)" stroke-width="3"/><circle cx="73" cy="73" r="71" fill="none" stroke="var(--brand)" stroke-width="3.5" stroke-dasharray="149 446" transform="rotate(60 73 73)"/><circle cx="73" cy="73" r="20" fill="var(--brand)"/></svg>
  <h5>Quillpost</h5><a href="#">⊙ Watch Video</a>
</div>
<div class="addon" style="left:890px">
  <svg class="ringset" width="146" height="146" viewBox="0 0 146 146"><circle cx="73" cy="73" r="71" fill="none" stroke="var(--ring)" stroke-width="3"/><circle cx="73" cy="73" r="71" fill="none" stroke="var(--green)" stroke-width="3.5" stroke-dasharray="149 446" transform="rotate(60 73 73)"/><text x="73" y="93" font-size="58" text-anchor="middle" fill="var(--green)" font-family="Lato,sans-serif">$</text></svg>
  <h5>Payment</h5><a href="#">⊙ Watch Video</a>
</div>
</body>
</html>
```